Calloway needs a modernized design

We would like a modern update (that can be responsive) to our existing website. Attached are the two existing pages we would like new concepts of - our home page and a page about one of our locations.

Calloway is provides executive offices and virtual office services. Startups, law firms, and financial services are our primary clients. We would like a professional, clean design, leaning towards minimalist. We intend to greatly reduce/eliminate the long paragraphs of text.

Requirements
Must have
• A design that can be responsive
Nice to have
• Large image(s) on home page that rotate.

```html
<!DOCTYPE html>
<html lang="en">
<head>
<meta charset="utf-8">
<title>Calloway Business Centers</title>
<link href="https://fonts.googleapis.com/css2?family=Source+Sans+3:wght@300;400;600&display=swap" rel="stylesheet">
<style>
:root{
  --navy:#243a6e;
  --suite:#2c4a95;
  --meeting:#f2a81d;
  --training:#e35a3e;
  --virtual:#6cbf45;
  --video:#8a3cc7;
  --accent-red:#e0553a;
  --contact-green:#5fb146;
  --light-grey:#b5b5b5;
  --line:#dcdcdc;
  --share-band:#f3f3f3;
  --footer:#272727;
  --white:#ffffff;
}
*{margin:0;padding:0;box-sizing:border-box}
html,body{width:1200px;height:2187px;overflow:hidden;background:var(--white)}
body{position:relative;font-family:"Source Sans 3","Source Sans Pro",sans-serif;color:#555}
.abs{position:absolute}

/* header */
.site-header{left:0;top:0;width:1200px;height:95px}
.brand{left:0;top:0;width:356px;height:95px;background:var(--white);display:flex;align-items:center;padding-left:133px;gap:10px}
.brand-dot{width:40px;height:40px;border-radius:50%;background:var(--navy)}
.brand-name{font-size:26px;font-weight:600;color:var(--navy);letter-spacing:.5px}
.nav-band{left:356px;top:0;width:844px;height:95px;background:var(--navy)}
.main-nav{left:419px;top:41px;width:450px;display:flex;white-space:nowrap;font-size:10.5px;color:var(--white);text-transform:uppercase}
.main-nav span{padding:0 8px;border-left:1px solid rgba(255,255,255,.6);line-height:12px}
.main-nav span:first-child{padding-left:0;border-left:0;text-decoration:underline}
.phone-box{left:891px;top:34px;width:26px;height:26px;border:1px solid var(--white)}
.phone-box svg{position:absolute;left:5px;top:5px}
.phones{left:923px;top:27px;font-size:13px;line-height:19px;color:var(--white);font-weight:600;white-space:nowrap}

/* hero */
.hero{left:0;top:95px;width:1200px;height:517px;background:linear-gradient(100deg,#d8dde2 0%,#b9c1c7 30%,#8d959b 55%,#4a4f56 75%,#6d747b 100%)}
.hero-arrow{top:345px}
.badge{left:556px;top:566px;width:88px;height:88px;border-radius:50%;background:#9aa3ad;border:5px solid var(--navy)}

/* services */
.section-title{left:0;top:695px;width:1200px;text-align:center;font-size:36px;font-weight:300;color:var(--light-grey)}
.service{display:flex;gap:12px;width:440px}
.service-icon{width:70px;height:70px;border-radius:50%;border:1px solid;flex:none;display:flex;align-items:center;justify-content:center}
.service-icon i{display:flex;width:58px;height:58px;border-radius:50%;align-items:center;justify-content:center}
.service h3{font-size:22px;font-weight:400;line-height:26px;margin-top:2px;white-space:nowrap}
.service p{font-size:10px;line-height:16px;color:var(--light-grey);margin-top:4px;width:360px}
.suite{left:134px;top:778px}.suite .service-icon{border-color:var(--suite)}.suite i{background:var(--suite)}.suite h3{color:var(--suite)}
.meeting{left:627px;top:778px}.meeting .service-icon{border-color:var(--meeting)}.meeting i{background:var(--meeting)}.meeting h3{color:var(--meeting)}
.training{left:134px;top:897px}.training .service-icon{border-color:var(--training)}.training i{background:var(--training)}.training h3{color:var(--training)}
.virtual{left:627px;top:897px}.virtual .service-icon{border-color:var(--virtual)}.virtual i{background:var(--virtual)}.virtual h3{color:var(--virtual)}
.video{left:381px;top:1016px}.video .service-icon{border-color:var(--video)}.video i{background:var(--video)}.video h3{color:var(--video)}

/* banner */
.why-band{left:0;top:1146px;width:1200px;height:105px;background:var(--navy);color:var(--white);text-align:center;font-size:22px;font-weight:300;line-height:31px;padding-top:21px}

/* videos */
.video-tile{top:1251px;height:321px;width:600px}
.video-left{left:0;background:linear-gradient(160deg,#6e7f99,#3d4c68 60%,#2b3550)}
.video-right{left:600px;background:linear-gradient(160deg,#5b6676,#8a939c 50%,#2a2e35)}
.play{position:absolute;left:50%;top:50%;margin:-35px 0 0 -35px}

/* features */
.feature{width:287px}
.feature-photo{width:287px;height:167px}
.feature h3{font-size:23px;font-weight:400;color:var(--accent-red);margin-top:16px;line-height:28px}
.feature p{font-size:10px;line-height:17.5px;color:#8a8a8a;margin-top:5px}
.btn-more{display:inline-block;margin-top:14px;background:#e6e6e6;color:#888;font-size:10px;width:71px;height:32px;line-height:32px;text-align:center}
.value{left:133px;top:1645px}.value .feature-photo{background:linear-gradient(135deg,#6d7a8c,#b6b0a2 55%,#454a52)}
.community{left:451px;top:1645px}.community .feature-photo{background:linear-gradient(135deg,#c7ccd1,#8e969f 55%,#e2e3e4)}

/* contact */
.contact{left:767px;top:1638px;width:300px}
.contact h3{font-size:24px;font-weight:400;color:var(--contact-green)}
.contact-grid{display:grid;grid-template-columns:146px 146px;gap:12px 8px;margin-top:10px}
.field{height:32px;border:1px solid var(--line);font-size:9.5px;color:#888;padding:10px 12px;position:relative;white-space:nowrap}
.field.select::after{content:"";position:absolute;right:12px;top:11px;width:5px;height:5px;border-right:1px solid #888;border-bottom:1px solid #888;transform:rotate(45deg)}
.field.message{grid-column:1/3;height:98px}
.btn-submit{margin-top:16px;width:57px;height:32px;background:#3a3a3a;color:var(--white);font-size:10px;line-height:32px;text-align:center}

/* share */
.share-band{left:0;top:2027px;width:1200px;height:80px;background:var(--share-band);display:flex;align-items:center;justify-content:center;gap:5px;font-size:14px;color:#8f8f8f}
.share-band .lbl{margin-right:6px}
.share-dot{width:24px;height:24px;border-radius:50%}

/* footer */
.site-footer{left:0;top:2107px;width:1200px;height:80px;background:var(--footer)}
.footer-links{left:133px;top:2127px;display:flex;font-size:9.5px;color:#cfcfcf;white-space:nowrap}
.footer-links span{padding:0 7px;border-left:1px solid #777;line-height:11px}
.footer-links span:first-child{padding-left:0;border-left:0}
.copyright{left:133px;top:2154px;font-size:9.5px;color:#aaa}
.footer-brand{left:936px;top:2124px;display:flex;align-items:center;gap:8px}
.footer-brand .brand-dot{width:34px;height:34px;background:#555}
.footer-brand span{font-size:19px;font-weight:600;color:#666}
</style>
</head>
<body>

<header class="site-header abs">
  <div class="brand abs"><div class="brand-dot"></div><span class="brand-name">Calloway</span></div>
  <div class="nav-band abs"></div>
  <nav class="main-nav abs">
    <span>Home</span><span>Properties</span><span>Virtual Tours &amp; Videos</span><span>Photos</span><span>Broker Referrals</span>
  </nav>
  <div class="phone-box abs">
    <svg width="14" height="14" viewBox="0 0 24 24"><path fill="#fff" d="M6.6 10.8a15.1 15.1 0 0 0 6.6 6.6l2.2-2.2c.3-.3.7-.4 1-.2 1.1.4 2.3.6 3.6.6.6 0 1 .4 1 1V20c0 .6-.4 1-1 1A17 17 0 0 1 3 4c0-.6.4-1 1-1h3.5c.6 0 1 .4 1 1 0 1.3.2 2.5.6 3.6.1.3 0 .7-.2 1z"/></svg>
  </div>
  <div class="phones abs">Dallas - 214.555.0142<br>Houston - 713.555.0187</div>
</header>

<section class="hero abs" role="img" aria-label="Rotating photo of a professional working at a desktop computer in a bright shared office"></section>
<svg class="hero-arrow abs" style="left:22px" width="14" height="26" viewBox="0 0 14 26"><path d="M12 2 2 13l10 11" fill="none" stroke="#444" stroke-width="2"/></svg>
<svg class="hero-arrow abs" style="left:1158px" width="14" height="26" viewBox="0 0 14 26"><path d="m2 2 10 11L2 24" fill="none" stroke="#444" stroke-width="2"/></svg>
<div class="badge abs"></div>

<h2 class="section-title abs">Our Services</h2>

<div class="service suite abs">
  <div class="service-icon"><i><svg width="20" height="24" viewBox="0 0 20 24"><rect x="3" y="1" width="14" height="22" fill="none" stroke="#fff" stroke-width="2"/><path d="M7 6h2M11 6h2M7 10h2M11 10h2M7 14h2M11 14h2" stroke="#fff" stroke-width="2"/></svg></i></div>
  <div><h3>Executive Office Suites</h3><p>Private furnished suites with staffed reception, fast internet and flexible terms for growing teams.</p></div>
</div>
<div class="service meeting abs">
  <div class="service-icon"><i><svg width="26" height="20" viewBox="0 0 26 20"><circle cx="13" cy="6" r="4" fill="#fff"/><circle cx="5" cy="8" r="3" fill="#fff"/><circle cx="21" cy="8" r="3" fill="#fff"/><path d="M6 19a7 7 0 0 1 14 0zM0 19a5 5 0 0 1 8-4M26 19a5 5 0 0 0-8-4" fill="#fff"/></svg></i></div>
  <div><h3>On-Demand Meeting Rooms</h3><p>Book polished meeting rooms by the hour with screens, coffee service and friendly support.</p></div>
</div>
<div class="service training abs">
  <div class="service-icon"><i><svg width="22" height="20" viewBox="0 0 22 20"><path d="M1 1v18h20" fill="none" stroke="#fff" stroke-width="2"/><path d="M6 16V10M10 16V6M14 16V9M18 16V4" stroke="#fff" stroke-width="2.5"/></svg></i></div>
  <div><h3>On-Demand Training Rooms</h3><p>Spacious training rooms ready for workshops, seminars and onboarding days with all equipment included.</p></div>
</div>
<div class="service virtual abs">
  <div class="service-icon"><i><svg width="24" height="22" viewBox="0 0 24 22"><circle cx="9" cy="13" r="5" fill="none" stroke="#fff" stroke-width="3" stroke-dasharray="3 2"/><circle cx="9" cy="13" r="2" fill="#fff"/><circle cx="18" cy="6" r="3.5" fill="none" stroke="#fff" stroke-width="2.5" stroke-dasharray="2 1.5"/></svg></i></div>
  <div><h3>Virtual Office Solutions</h3><p>A prestigious business address, mail handling and call answering without leasing a full office.</p></div>
</div>
<div class="service video abs">
  <div class="service-icon"><i><svg width="24" height="16" viewBox="0 0 24 16"><rect x="1" y="2" width="15" height="12" rx="2" fill="#fff"/><path d="m17 6 6-4v12l-6-4z" fill="#fff"/></svg></i></div>
  <div><h3>Video Conference Solutions</h3><p>Connect with clients anywhere through studio quality video rooms set up and tested for you.</p></div>
</div>

<div class="why-band abs">See Why Smarter Companies are Choosing Calloway Business Centers' Dallas, Ft. Worth and<br>Houston Executive Office Suites, Virtual Offices, Meeting Rooms and Video Conferencing.</div>

<div class="video-tile video-left abs" role="img" aria-label="Video still of business people walking through a glass-walled office lobby">
  <svg class="play" width="70" height="70" viewBox="0 0 70 70"><circle cx="35" cy="35" r="33" fill="none" stroke="#fff" stroke-width="4"/><path d="M27 21v28l22-14z" fill="#fff"/></svg>
</div>
<div class="video-tile video-right abs" role="img" aria-label="Video still of two business people shaking hands by a window overlooking a city">
  <svg class="play" width="70" height="70" viewBox="0 0 70 70"><circle cx="35" cy="35" r="33" fill="none" stroke="#fff" stroke-width="4"/><path d="M27 21v28l22-14z" fill="#fff"/></svg>
</div>

<article class="feature value abs">
  <div class="feature-photo" role="img" aria-label="Photo of smiling colleagues reviewing work on a laptop"></div>
  <h3>Value</h3>
  <p>Either you need Dallas/Ft. Worth Office Space, Dallas Executive Suites, Ft. Worth Executive Suites, Houston Office Space, Houston Executive Suites, or maybe you simply need...</p>
  <span class="btn-more">Read more</span>
</article>
<article class="feature community abs">
  <div class="feature-photo" role="img" aria-label="Photo of a team meeting around a conference table"></div>
  <h3>Community</h3>
  <p>Either you need Dallas/Ft. Worth Office Space, Dallas Executive Suites, Ft. Worth Executive Suites, Houston Office Space, Houston Executive Suites, or maybe you simply need...</p>
  <span class="btn-more">Read more</span>
</article>

<form class="contact abs">
  <h3>Contact us</h3>
  <div class="contact-grid">
    <div class="field">Name</div><div class="field">Company</div>
    <div class="field">Phone</div><div class="field">Email</div>
    <div class="field select">Property Interested In:</div><div class="field select">Product Interested In:</div>
    <div class="field message">Message</div>
  </div>
  <div class="btn-submit">Submit</div>
</form>

<div class="share-band abs">
  <span class="lbl">Share this on :</span>
  <span class="share-dot" style="background:#3b5998"></span>
  <span class="share-dot" style="background:#33a8e0"></span>
  <span class="share-dot" style="background:#dd4b39"></span>
  <span class="share-dot" style="background:#5fb146"></span>
</div>

<footer class="site-footer abs"></footer>
<div class="footer-links abs">
  <span>About Us</span><span>Contact Us</span><span>Forms</span><span>Testimonials</span><span>FAQs</span><span>Careers</span><span>Furniture</span><span>Specials</span><span>Site Map</span><span>Privacy</span>
</div>
<div class="copyright abs">Copyright © 2016 Calloway Offices. All rights reserved.</div>
<div class="footer-brand abs"><div class="brand-dot"></div><span>Calloway</span></div>

</body>
</html>
```